Brellwick Partners, LLC Stationary

Brellwick Partners, LLC is a new financial planning and consulting company. We are looking for designs on business cards, letterhead, envelopes, and anything else that would be useful. Our preference for business card design is two sided. We are looking for a professional and clean look with incorporating the logo and patriotic feel. Thank you to all who participate and good luck!

```html
<!DOCTYPE html>
<html lang="en">
<head>
<meta charset="utf-8">
<title>Brellwick Partners, LLC – Business Card</title>
<link rel="stylesheet" href="https://fonts.googleapis.com/css2?family=Montserrat:wght@500;600&family=Open+Sans:wght@400;600;700&display=swap">
<style>
  :root {
    --navy: #123a66;
    --navy-deep: #0d2c52;
    --red: #c3262e;
    --white: #ffffff;
    --paper-shade: #e6e6e6;
    --ink-grey: #55585c;
    --backdrop: #ecebe8;
  }
  * { margin: 0; padding: 0; box-sizing: border-box; }
  html, body {
    width: 1200px;
    height: 950px;
    overflow: hidden;
    background: var(--backdrop);
  }
  .canvas {
    position: relative;
    width: 1200px;
    height: 950px;
  }
  .card {
    position: absolute;
    left: 290px;
    width: 620px;
    height: 354px;
    overflow: hidden;
    box-shadow: 0 6px 18px rgba(0, 0, 0, 0.18);
  }

  /* Back side */
  .card-back {
    top: 84px;
    background: linear-gradient(120deg, var(--white) 30%, var(--paper-shade) 100%);
  }
  .brand-lockup {
    position: absolute;
    left: 0;
    right: 0;
    top: 118px;
    display: flex;
    flex-direction: column;
    align-items: center;
  }
  .brand-name {
    display: flex;
    align-items: center;
    gap: 14px;
    font-family: "Montserrat", sans-serif;
    font-weight: 600;
    font-size: 30px;
    letter-spacing: 2px;
    color: var(--navy);
  }
  .brand-mark {
    width: 14px;
    height: 14px;
    border-radius: 50%;
    background: var(--navy);
  }
  .brand-tagline {
    margin-top: 10px;
    padding-top: 6px;
    border-top: 1px solid var(--red);
    font-family: "Open Sans", sans-serif;
    font-size: 10px;
    letter-spacing: 2px;
    color: var(--ink-grey);
    text-transform: uppercase;
  }
  .back-web {
    position: absolute;
    left: 0;
    right: 0;
    top: 262px;
    text-align: center;
    font-family: "Open Sans", sans-serif;
    font-size: 15px;
    letter-spacing: 4px;
    color: var(--ink-grey);
  }

  /* Front side */
  .card-front {
    top: 510px;
    background: var(--white);
  }
  .front-panel {
    position: absolute;
    inset: 0;
  }
  .holder {
    position: absolute;
    left: 34px;
    top: 30px;
    font-family: "Open Sans", sans-serif;
    color: var(--white);
  }
  .holder-name {
    font-weight: 700;
    font-size: 19px;
    letter-spacing: 0.5px;
  }
  .holder-title {
    font-size: 14px;
    letter-spacing: 0.5px;
    margin-top: 2px;
  }
  .contact {
    position: absolute;
    left: 34px;
    top: 150px;
    font-family: "Open Sans", sans-serif;
    font-size: 15px;
    line-height: 21px;
    color: var(--white);
    list-style: none;
  }
  .contact-address { margin-bottom: 2px; }
  .contact-line {
    display: flex;
    align-items: center;
    gap: 7px;
  }
  .contact-icon {
    width: 13px;
    height: 13px;
    flex: none;
  }
</style>
</head>
<body>
<main class="canvas">

  <section class="card card-back" aria-label="Business card, back side">
    <div class="brand-lockup">
      <div class="brand-name"><span class="brand-mark"></span>BRELLWICK PARTNERS, LLC</div>
      <div class="brand-tagline">Financial Planning and Consulting</div>
    </div>
    <p class="back-web">www.brellwick.com</p>
  </section>

  <section class="card card-front" aria-label="Business card, front side">
    <svg class="front-panel" width="620" height="354" viewBox="0 0 620 354" aria-hidden="true">
      <defs>
        <linearGradient id="panel-fill" x1="0" y1="0" x2="1" y2="1">
          <stop offset="0" stop-color="#174476"/>
          <stop offset="1" stop-color="#0d2c52"/>
        </linearGradient>
      </defs>
      <rect x="0" y="0" width="372" height="354" fill="url(#panel-fill)"/>
    </svg>

    <div class="holder">
      <div class="holder-name">DANIEL MARSH</div>
      <div class="holder-title">PRESIDENT</div>
    </div>

    <ul class="contact">
      <li class="contact-address">2716 Harrow Lane<br>Fairmont Hills, NY 11420</li>
      <li class="contact-line">
        <svg class="contact-icon" viewBox="0 0 16 16" aria-hidden="true"><path fill="#fff" d="M2 6c0-2 2-3 6-3s6 1 6 3l-3 1-1-2H6L5 7 2 6zM4 8h8l2 6H2l2-6zm4 1.5a2 2 0 1 0 0 4 2 2 0 0 0 0-4z"/></svg>
        555 0142 7781
      </li>
      <li class="contact-line">
        <svg class="contact-icon" viewBox="0 0 16 16" aria-hidden="true"><path fill="#fff" d="M4 1h8v4H4zM1 6h14v6h-2v3H3v-3H1zm4 4v4h6v-4z"/></svg>
        555 0198 3064
      </li>
      <li class="contact-line">
        <svg class="contact-icon" viewBox="0 0 16 16" aria-hidden="true"><path fill="#fff" d="M1 3h14v10H1zm1.5 1.2L8 8.5l5.5-4.3z"/></svg>
        daniel@brellwick.com
      </li>
      <li class="contact-line">
        <svg class="contact-icon" viewBox="0 0 16 16" aria-hidden="true"><circle cx="8" cy="8" r="7" fill="none" stroke="#fff" stroke-width="1.6"/><path d="M1 8h14M8 1c-3 3.5-3 10.5 0 14M8 1c3 3.5 3 10.5 0 14" fill="none" stroke="#fff" stroke-width="1.2"/></svg>
        www.brellwick.com
      </li>
    </ul>
  </section>

</main>
</body>
</html>
```